Business Card for premium dental clinic

We are a premium dental clinic based in Brasov, Romania with more than 15 year on the market, providing quality dental treatment made by a team of more specialized dentists, working with modern equipment as a solution to beautiful and healthy teeth.

Our current logo for the clinic use 2 square with colors black and gold - dr Ternisu - studio, using family fonts Bodoni, Myriad Pro and Segoe Print.
Depending on the printing we used some gold CMYK background or gold foil picture background or a gold gradient.
We want a business card:
- eye catching business card
- distinguished business card
- premium design
- to keep the color scheme of black and gold
- to attract the customers to spent time reading the information
- modern concept

```html
<!DOCTYPE html>
<html lang="en">
<head>
<meta charset="utf-8">
<title>dr Ternisu studio – business card</title>
<link href="https://fonts.googleapis.com/css2?family=Open+Sans:wght@400;600&family=Roboto+Condensed:wght@400&display=swap" rel="stylesheet">
<style>
  :root {
    --page: #ffffff;
    --card-black: #231f20;
    --gold: #f2c14e;
    --gold-light: #f7d774;
    --gold-mid: #e0a92c;
    --gold-deep: #b7851c;
    --ink: #231f20;
    --white: #ffffff;
  }
  * { margin: 0; padding: 0; box-sizing: border-box; }
  html, body {
    width: 1199px; height: 1200px; overflow: hidden;
    background: var(--page);
    font-family: "Open Sans", Arial, sans-serif;
  }
  .canvas { position: relative; width: 1199px; height: 1200px; }

  .card {
    position: absolute; left: 330px; width: 540px; height: 300px;
    background: var(--card-black);
  }
  .card--front { top: 192px; }
  .card--back { top: 708px; }

  .foil {
    background: linear-gradient(135deg, var(--gold-light) 0%, var(--gold) 30%, var(--gold-mid) 55%, var(--gold-light) 75%, var(--gold-deep) 100%);
  }

  /* front: name plate */
  .name-plate {
    position: absolute; left: 0; top: 47px; width: 190px; height: 53px;
    border-radius: 0 6px 6px 0;
  }
  .name-plate__name {
    position: absolute; left: 24px; top: 2px;
    font-size: 27px; line-height: 36px; color: var(--ink); letter-spacing: -0.3px;
  }
  .name-plate__title {
    position: absolute; left: 68px; top: 36px;
    font-size: 8px; line-height: 10px; letter-spacing: 4px; color: var(--ink);
  }

  /* front: small logo block */
  .brand-box {
    position: absolute; left: 272px; top: 35px; width: 232px; height: 116px;
    border: 1.5px solid var(--white); overflow: hidden;
  }
  .brand-box__foil { position: absolute; left: 0; top: 0; width: 115px; height: 100%; }
  .brand-box__name {
    position: absolute; left: 126px; top: 22px; width: 100px;
    font-size: 16px; line-height: 20px; color: var(--white);
  }
  .brand-box__tag {
    position: absolute; right: 6px; bottom: 4px;
    font-family: "Roboto Condensed", "Arial Narrow", sans-serif;
    font-weight: 400; font-size: 13px; line-height: 16px; color: var(--white);
  }

  /* front: contact list */
  .contacts { position: absolute; left: 26px; top: 178px; list-style: none; }
  .contacts__item {
    display: flex; align-items: center; height: 24px;
    font-size: 16.5px; color: var(--gold);
  }
  .contacts__icon { width: 16px; height: 16px; margin-right: 18px; flex: none; }
  .address {
    position: absolute; left: 273px; top: 250px;
    display: flex; align-items: center;
    font-size: 16.5px; color: var(--gold);
  }
  .address .contacts__icon { margin-right: 6px; }

  /* back */
  .back-frame {
    position: absolute; left: 19px; top: 25px; width: 500px; height: 248px;
    border: 2.5px solid var(--white); overflow: hidden;
  }
  .back-frame__foil { position: absolute; left: 0; top: 0; width: 248px; height: 100%; }
  .back-frame__name {
    position: absolute; left: 270px; top: 52px; width: 210px;
    font-size: 32px; line-height: 40px; color: var(--white);
  }
  .back-frame__tag {
    position: absolute; right: 10px; bottom: 8px;
    font-family: "Roboto Condensed", "Arial Narrow", sans-serif;
    font-weight: 400; font-size: 28px; line-height: 34px; color: var(--white);
  }
</style>
</head>
<body>
<main class="canvas">

  <section class="card card--front" aria-label="Business card front">
    <div class="name-plate foil">
      <span class="name-plate__name">YourName</span>
      <span class="name-plate__title">TITLE</span>
    </div>

    <div class="brand-box">
      <div class="brand-box__foil foil" role="img" aria-label="Gold foil texture"></div>
      <span class="brand-box__name">dr ternisu<br>studio</span>
      <span class="brand-box__tag">dental clinic</span>
    </div>

    <ul class="contacts">
      <li class="contacts__item">
        <svg class="contacts__icon" viewBox="0 0 16 16" fill="none" stroke="#f2c14e" stroke-width="1.4"><rect x="4" y="1" width="8" height="14" rx="1.2"/><line x1="7" y1="12.5" x2="9" y2="12.5"/></svg>
        +1234567890
      </li>
      <li class="contacts__item">
        <svg class="contacts__icon" viewBox="0 0 16 16" fill="#f2c14e"><path d="M3.5 1.5l2.4 2.8-1.3 1.7c.9 2.1 2.4 3.7 4.5 4.7l1.7-1.3 2.8 2.4-1.4 2.2C7 13.6 2.5 9.1 1.5 3z"/></svg>
        +1234567890
      </li>
      <li class="contacts__item">
        <svg class="contacts__icon" viewBox="0 0 16 16" fill="none" stroke="#f2c14e" stroke-width="1.4"><rect x="1" y="3.5" width="14" height="9"/><polyline points="1,3.5 8,9 15,3.5"/></svg>
        yourmail@mail.com
      </li>
      <li class="contacts__item">
        <svg class="contacts__icon" viewBox="0 0 16 16" fill="none" stroke="#f2c14e" stroke-width="1.2"><circle cx="8" cy="8" r="6.5"/><ellipse cx="8" cy="8" rx="3" ry="6.5"/><line x1="1.5" y1="8" x2="14.5" y2="8"/></svg>
        www.yoursite.com
      </li>
    </ul>

    <div class="address">
      <svg class="contacts__icon" viewBox="0 0 16 16" fill="none" stroke="#f2c14e" stroke-width="1.8"><path d="M8 15s5-5.2 5-8.6A5 5 0 0 0 3 6.4C3 9.8 8 15 8 15z"/><circle cx="8" cy="6.4" r="1.8"/></svg>
      123 Floor 1 Ny, suite 123
    </div>
  </section>

  <section class="card card--back" aria-label="Business card back">
    <div class="back-frame">
      <div class="back-frame__foil foil" role="img" aria-label="Gold foil texture"></div>
      <span class="back-frame__name">dr ternisu<br>studio</span>
      <span class="back-frame__tag">dental clinic</span>
    </div>
  </section>

</main>
</body>
</html>
```